Visitenkarten-Design für das Business mit Gesundheit& Beauty
Zielgruppe
Ich bin selbständige Vertriebspartnerin von Vk. Die Visitenkarten sollen nicht zu verspielt wirken, eher geschäftlich. Dennoch könnte eine Verbindung zu den Bereichen Gesundheit & Beuuty dazukommen .
Hauptproduktmerkmal ist zum Beispiel die Aloe Vera, Naturprodukte.. mehr Infos auf : www.bettina-kolmar-beispiel.de
Instagram :bettikolmar
Eventuell könnte mein Slogan mit 'just more' noch einfließen, muss aber nicht. Bin für Ideen offen...
Aufgabenstellung
elegant und zeitlos, aber weich
Vielleicht eine goldene Aloe Vera irgendwie mit drauf?
Habe bei den dateien mal ein paar Screenshots hinzugefügt was ich recht schön fand

```html
<!DOCTYPE html>
<html lang="de">
<head>
<meta charset="utf-8">
<title>Visitenkarte – Bettina Kolmar</title>
<link rel="stylesheet" href="https://fonts.googleapis.com/css2?family=Montserrat:wght@400;500;600&display=swap">
<style>
  :root {
    --backdrop: #ece9e4;
    --card-white: #ffffff;
    --ink: #2a2a2a;
    --gold: #b08d68;
    --beige-light: #ddd0bb;
    --beige-dark: #c7b595;
    --sage: #a9ab8a;
    --shadow: rgba(40, 30, 20, 0.18);
  }
  * { box-sizing: border-box; margin: 0; padding: 0; }
  html, body {
    width: 1200px;
    height: 900px;
    overflow: hidden;
    background: var(--backdrop);
    font-family: "Montserrat", sans-serif;
    color: var(--ink);
  }
  .sheet {
    width: 1200px;
    height: 900px;
    display: flex;
    flex-direction: column;
    align-items: center;
    justify-content: center;
    gap: 56px;
  }
  .card {
    position: relative;
    width: 620px;
    height: 370px;
    box-shadow: 0 10px 30px var(--shadow);
    overflow: hidden;
  }
  .card--front { background: var(--card-white); }

  .brand-name {
    font-family: "Montserrat", sans-serif;
    font-weight: 400;
    letter-spacing: 0.14em;
    color: var(--ink);
    text-transform: uppercase;
    white-space: nowrap;
  }
  .card--front .brand-name {
    position: absolute;
    top: 72px;
    right: 56px;
    font-size: 27px;
  }

  .contact-block {
    position: absolute;
    left: 48px;
    bottom: 52px;
  }
  .person-name {
    font-size: 19px;
    font-weight: 600;
    letter-spacing: 0.06em;
    color: var(--gold);
    text-transform: uppercase;
  }
  .person-role {
    font-size: 14px;
    margin-top: 4px;
    margin-bottom: 18px;
  }
  .contact-list { list-style: none; }
  .contact-item {
    display: flex;
    align-items: center;
    gap: 14px;
    font-size: 15px;
    line-height: 24px;
    letter-spacing: 0.03em;
  }
  .contact-icon {
    width: 13px;
    height: 13px;
    fill: var(--gold);
    flex: none;
  }

  .card--back .pattern-fill {
    position: absolute;
    inset: 0;
    width: 100%;
    height: 100%;
  }
  .card--back .brand-name {
    position: absolute;
    top: 50%;
    left: 50%;
    transform: translate(-50%, -50%);
    font-size: 32px;
  }
</style>
</head>
<body>
<main class="sheet">

  <section class="card card--front" aria-label="Vorderseite">
    <div class="brand-name">Bettina Kolmar</div>

    <div class="contact-block">
      <div class="person-name">Jonas Albrecht</div>
      <div class="person-role">Australasian</div>
      <ul class="contact-list">
        <li class="contact-item">
          <svg class="contact-icon" viewBox="0 0 24 24" aria-hidden="true"><path d="M6.6 10.8a15.1 15.1 0 0 0 6.6 6.6l2.2-2.2c.3-.3.7-.4 1-.2 1.1.4 2.3.6 3.6.6.6 0 1 .4 1 1V20c0 .6-.4 1-1 1C10.6 21 3 13.4 3 4c0-.6.4-1 1-1h3.5c.6 0 1 .4 1 1 0 1.3.2 2.5.6 3.6.1.3 0 .7-.2 1z"/></svg>
          <span>254 555 0193</span>
        </li>
        <li class="contact-item">
          <svg class="contact-icon" viewBox="0 0 24 24" aria-hidden="true"><path d="M2 5h20v14H2zm2 2v.5l8 5 8-5V7zm0 2.8V17h16V9.8l-8 5z"/></svg>
          <span>j.albrecht@example.com</span>
        </li>
        <li class="contact-item">
          <svg class="contact-icon" viewBox="0 0 24 24" aria-hidden="true"><path d="M12 2a10 10 0 1 0 0 20 10 10 0 0 0 0-20zm6.9 9h-3a15.6 15.6 0 0 0-1.3-6 8 8 0 0 1 4.3 6zM12 4c.9 1.3 1.7 3.8 1.9 7h-3.8c.2-3.2 1-5.7 1.9-7zM9.4 5a15.6 15.6 0 0 0-1.3 6h-3a8 8 0 0 1 4.3-6zM5.1 13h3a15.6 15.6 0 0 0 1.3 6 8 8 0 0 1-4.3-6zM12 20c-.9-1.3-1.7-3.8-1.9-7h3.8c-.2 3.2-1 5.7-1.9 7zm2.6-1a15.6 15.6 0 0 0 1.3-6h3a8 8 0 0 1-4.3 6z"/></svg>
          <span>www.kolmar-beispiel.de</span>
        </li>
        <li class="contact-item">
          <svg class="contact-icon" viewBox="0 0 24 24" aria-hidden="true"><path d="M12 2a7 7 0 0 0-7 7c0 5.2 7 13 7 13s7-7.8 7-13a7 7 0 0 0-7-7zm0 9.5a2.5 2.5 0 1 1 0-5 2.5 2.5 0 0 1 0 5z"/></svg>
          <span>48 Linden Road, CT 06300</span>
        </li>
      </ul>
    </div>
  </section>

  <section class="card card--back" aria-label="Rückseite">
    <svg class="pattern-fill" viewBox="0 0 620 370" preserveAspectRatio="none" role="img" aria-label="Zarte Aquarell-Blätterranken in Gold und Salbeigrün auf beigem Grund">
      <defs>
        <linearGradient id="back-tone" x1="0" y1="0" x2="1" y2="1">
          <stop offset="0" stop-color="#ddd0bb"/>
          <stop offset="0.6" stop-color="#d2c2a6"/>
          <stop offset="1" stop-color="#c7b595"/>
        </linearGradient>
      </defs>
      <rect width="620" height="370" fill="url(#back-tone)"/>
    </svg>
    <div class="brand-name">Bettina Kolmar</div>
  </section>

</main>
</body>
</html>
```